Flat Belly Design Graphics for Social

I want to create 9 social media graphics (new Instagram size 4:5 (1080 x 1350 pixels) focusing on our Flat Belly Graphics, using the pics attached. Use the attached pics, NO RANDOM STOCK PHOTOGRAPHY. For the color scheme of the graphics, the color palette is attached. YOU MUST POST ALL 9 GRAPHICS IN ONE ENTRY.
Using the 3 titles below, create one set of graphics. 1) with all text, then for the others, use the pictures as detailed below in IMPORTANT:
1. Ten-Week Bright Morning Reboot
2. The Quick Garden Kitchen Menu Guide
3. Studio Habits for Lasting Energy Past Midlife - Zero Gym Needed
IMPORTANT:
Only use RK Pic 1 and RK Pic 2 with the title, Ten-Week Bright Morning Reboot
Only use meal plan1 and meal plan2 pics with the title, Quick Garden Kitchen Menu Guide
Only use studio habits 1 and studio habits 2 pics with the title, Studio Habits for Lasting Energy Past Midlife - Zero Gym Needed
women over 40

```html
<!DOCTYPE html>
<html lang="en">
<head>
<meta charset="utf-8">
<title>Morning Reboot Social Set</title>
<link rel="stylesheet" href="https://fonts.googleapis.com/css2?family=Anton&family=Montserrat:wght@300;600;700;800;900&family=Playfair+Display:ital,wght@1,500;1,600&family=Great+Vibes&display=swap">
<style>
  :root{
    --stage:#262626;
    --blush:#fbecee;
    --rose:#e497ad;
    --forest:#175c50;
    --slate:#2a4a46;
    --teal:#247868;
    --magenta:#d2578f;
    --white:#ffffff;
    --wood:#3b2a20;
    --skin:#b98a73;
  }
  *{margin:0;padding:0;box-sizing:border-box}
  html,body{width:960px;height:1200px;overflow:hidden;background:var(--stage)}
  .board{position:relative;width:960px;height:1200px}
  .post{position:absolute;width:231px;height:289px;overflow:hidden;background:var(--blush)}
  .post > *{position:absolute}
  .c1{left:110px}.c2{left:363px}.c3{left:617px}
  .r1{top:132px}.r2{top:452px}.r3{top:772px}
  .wide{font-family:"Montserrat",sans-serif;font-weight:800;line-height:1;left:0;right:0;text-align:center}
  .tall{font-family:"Anton",sans-serif;line-height:1;text-transform:uppercase}
  .serif{font-family:"Playfair Display",serif;font-style:italic;line-height:1;left:0;right:0;text-align:center}
  .band{left:0;right:0}
  .photo{background:linear-gradient(160deg,#efe6e6,#c9a596 60%,#8a6656)}
  .food{background:linear-gradient(150deg,#6b3a2a,#a24c38 35%,#6d7a3c 65%,#3b2a20)}
</style>
</head>
<body>
<main class="board">

  <!-- Ten-Week Bright Morning Reboot, type only -->
  <section class="post c1 r1">
    <p class="wide" style="top:42px;font-size:33px;font-weight:900;color:var(--slate)">TEN-WEEK</p>
    <div class="band" style="top:102px;height:56px;background:var(--rose)"></div>
    <p class="wide" style="top:109px;font-size:40px;font-weight:300;color:var(--white)">BRIGHT</p>
    <p class="wide" style="top:170px;font-size:35px;font-weight:800;color:var(--slate)">MORNING</p>
    <p class="serif" style="top:240px;font-size:23px;font-weight:500;color:var(--magenta)">REBOOT</p>
  </section>

  <!-- Quick Garden Kitchen Menu Guide, type only -->
  <section class="post c2 r1">
    <p class="wide" style="top:30px;font-size:19px;font-weight:700;color:var(--forest)">THE QUICK</p>
    <p class="tall" style="top:60px;left:0;right:0;text-align:center;font-size:34px;color:var(--rose)">GARDEN KITCHEN</p>
    <div class="band" style="top:120px;height:136px;background:var(--forest)"></div>
    <p class="wide" style="top:134px;font-size:50px;font-weight:600;color:var(--white)">MENU</p>
    <p class="wide" style="top:190px;font-size:50px;font-weight:600;color:var(--white)">GUIDE</p>
  </section>

  <!-- Studio Habits, type only -->
  <section class="post c3 r1">
    <div class="band" style="top:0;height:110px;background:var(--rose)"></div>
    <p class="wide" style="top:16px;font-size:37px;font-weight:800;color:var(--blush)">STUDIO</p>
    <p class="wide" style="top:58px;font-size:37px;font-weight:800;color:var(--blush)">HABITS</p>
    <p style="top:118px;left:0;right:0;text-align:center;font-family:'Great Vibes',cursive;font-size:30px;color:var(--forest);line-height:1">for</p>
    <p class="wide" style="top:158px;font-size:23px;color:var(--forest)">LASTING ENERGY</p>
    <p class="wide" style="top:192px;font-size:29px;color:var(--rose)">PAST MIDLIFE</p>
    <div class="band" style="top:242px;height:34px;background:var(--forest)"></div>
    <p class="wide" style="top:251px;font-size:16px;font-weight:700;color:var(--white)">ZERO GYM NEEDED</p>
  </section>

  <!-- Ten-Week Bright Morning Reboot, photo 1 -->
  <section class="post c1 r2">
    <div class="photo" role="img" aria-label="Smiling woman in a white cropped sweater pointing to her waist" style="left:102px;top:0;width:129px;height:157px"></div>
    <p class="tall" style="top:18px;left:12px;font-size:58px;color:var(--teal)">TEN</p>
    <p class="tall" style="top:86px;left:12px;font-size:52px;color:var(--teal);letter-spacing:-1px">WEEK</p>
    <div class="band" style="top:157px;height:70px;background:var(--forest)"></div>
    <p class="tall" style="top:171px;left:0;right:0;text-align:center;font-size:34px;color:var(--white)">BRIGHT MORNING</p>
    <p class="tall" style="top:234px;left:0;right:0;text-align:center;font-size:28px;color:var(--magenta)">REBOOT</p>
  </section>

  <!-- Quick Garden Kitchen Menu Guide, photo 1 -->
  <section class="post c2 r2">
    <div class="food" role="img" aria-label="Table of fresh berries, chicken, vegetables and a printed menu sheet" style="left:0;top:144px;width:231px;height:145px"></div>
    <svg style="left:13px;top:7px" width="95" height="190" viewBox="0 0 95 190" aria-hidden="true">
      <polygon points="0,0 95,0 95,168 47.5,190 0,168" fill="var(--rose)"/>
    </svg>
    <p class="tall" style="top:28px;left:13px;width:95px;text-align:center;font-size:36px;color:var(--white)">THE</p>
    <p class="tall" style="top:72px;left:13px;width:95px;text-align:center;font-size:34px;color:var(--white)">QUICK</p>
    <p class="tall" style="top:134px;left:13px;width:95px;text-align:center;font-size:24px;color:var(--white)">GARDEN</p>
    <p class="wide" style="top:48px;left:110px;font-size:22px;font-weight:600;color:var(--slate)">KITCHEN</p>
    <p class="wide" style="top:88px;left:110px;font-size:26px;font-weight:600;color:var(--slate)">MENU</p>
    <p class="wide" style="top:252px;font-size:27px;font-weight:700;color:var(--white)">GUIDE</p>
  </section>

  <!-- Studio Habits, photo 1 -->
  <section class="post c3 r2">
    <div class="photo" role="img" aria-label="Two women sharing a whispered secret, one looking surprised" style="left:0;top:0;width:231px;height:155px"></div>
    <p class="tall" style="top:164px;left:10px;font-size:26px;color:var(--rose)">STUDIO HABITS</p>
    <p class="wide" style="top:201px;left:10px;text-align:left;font-size:20px;color:var(--forest)">FOR LASTING</p>
    <p class="wide" style="top:229px;left:10px;text-align:left;font-size:20px;color:var(--forest)">ENERGY</p>
    <p class="wide" style="top:259px;left:10px;text-align:left;font-size:18px;font-weight:700;color:var(--rose)">PAST MIDLIFE</p>
    <div style="left:143px;top:200px;width:110px;height:110px;border-radius:50%;background:var(--rose)"></div>
    <p class="wide" style="top:219px;left:148px;right:8px;text-align:right;font-size:13px;font-weight:700;color:var(--white);line-height:1.4">ZERO<br>GYM<br>NEEDED</p>
  </section>

  <!-- Ten-Week Bright Morning Reboot, photo 2 -->
  <section class="post c1 r3">
    <svg style="left:0;top:0" width="231" height="289" viewBox="0 0 231 289" aria-hidden="true">
      <polygon points="0,190 231,125 231,289 0,289" fill="var(--wood)"/>
    </svg>
    <div class="photo" role="img" aria-label="Smiling woman in a white cropped sweater pointing to her waist" style="left:27px;top:32px;width:191px;height:257px;border-radius:90px 90px 0 0"></div>
    <p class="tall" style="top:16px;left:10px;font-size:30px;color:var(--forest)">TEN</p>
    <p class="tall" style="top:52px;left:10px;font-size:30px;color:var(--forest)">WEEK</p>
    <p class="tall" style="top:18px;right:10px;text-align:right;font-size:32px;color:var(--forest)">BRIGHT</p>
    <p class="tall" style="top:58px;right:10px;text-align:right;font-size:24px;color:var(--forest)">MORNING</p>
    <p class="wide" style="top:257px;font-size:22px;font-weight:600;color:var(--white)">REBOOT</p>
  </section>

  <!-- Quick Garden Kitchen Menu Guide, photo 2 -->
  <section class="post c2 r3 food" role="img" aria-label="Overhead spread of tomatoes, bananas, greens, lentils and fresh produce on wood">
    <div style="left:22px;top:71px;width:186px;height:150px;background:var(--blush);border-radius:10px"></div>
    <p class="serif" style="top:92px;font-size:23px;font-weight:600;color:var(--forest)">The Quick</p>
    <p class="wide" style="top:128px;font-size:19px;font-weight:700;color:var(--slate)">GARDEN KITCHEN</p>
    <p class="wide" style="top:168px;font-size:28px;font-weight:700;color:var(--rose)">MENU GUIDE</p>
  </section>

  <!-- Studio Habits, photo 2 -->
  <section class="post c3 r3" style="background:var(--rose)">
    <div class="photo" role="img" aria-label="Two women sharing a whispered secret, one looking excited" style="left:90px;top:0;width:141px;height:185px"></div>
    <div style="left:-40px;top:-60px;width:160px;height:140px;border-radius:0 0 90px 0;background:var(--forest)"></div>
    <p class="tall" style="top:4px;left:12px;font-size:24px;color:var(--white)">STUDIO</p>
    <p class="tall" style="top:40px;left:12px;font-size:24px;color:var(--white)">HABITS</p>
    <p class="tall" style="top:84px;left:12px;font-size:18px;color:var(--white)">FOR</p>
    <p class="tall" style="top:108px;left:12px;font-size:28px;color:var(--white)">LASTING</p>
    <p class="tall" style="top:144px;left:12px;font-size:28px;color:var(--white)">ENERGY</p>
    <div class="band" style="top:185px;height:70px;background:var(--blush)"></div>
    <p class="tall" style="top:198px;left:0;right:0;text-align:center;font-size:38px;color:var(--forest)">PAST MIDLIFE</p>
    <p class="tall" style="top:262px;left:0;right:0;text-align:center;font-size:17px;color:var(--white)">ZERO GYM NEEDED</p>
  </section>

</main>
</body>
</html>
```